Simple and Clean business card design

We would like the design to be simple clean and to incorporate our colors.

We are open to your design and talent, we have the dots in our logo as we think of it as data points and we connect data points for people.

We are open to see the great creative and clean design you bring to the table

Contact Information for Business Card

please include: name, position, email, phone and website

Font styles to use
Sans Serif

Requirements
Must have
• my colors incorporated, simplicity
Nice to have
• lots of white space, simplicity
Should not have
• complexicity/ complex art

```html
<!DOCTYPE html>
<html lang="en">
<head>
<meta charset="UTF-8">
<title>Petalon Business Card</title>
<link href="https://fonts.googleapis.com/css2?family=Lato:wght@400;700;900&display=swap" rel="stylesheet">
<style>
  :root {
    --stage: #2a2b2d;
    --card-dark: #1c1d1f;
    --brand-blue: #4285f4;
    --brand-blue-deep: #2f6fdc;
    --brand-blue-light: #5b96f6;
    --ink-light: #ffffff;
    --rule: #4a4b4e;
  }
  * { margin: 0; padding: 0; box-sizing: border-box; }
  html, body {
    width: 1200px;
    height: 1108px;
    overflow: hidden;
    background: var(--stage);
    font-family: "Lato", sans-serif;
  }
  .stage {
    position: relative;
    width: 1200px;
    height: 1108px;
    display: flex;
    justify-content: center;
    align-items: center;
    gap: 70px;
  }
  .card {
    width: 400px;
    height: 700px;
    border-radius: 26px;
    position: relative;
    overflow: hidden;
  }
  .card--front {
    background: var(--card-dark);
    display: flex;
    flex-direction: column;
    align-items: center;
  }
  .wordmark {
    font-family: "Lato", sans-serif;
    font-weight: 900;
    color: var(--ink-light);
    letter-spacing: -1px;
    line-height: 1;
    display: flex;
    align-items: center;
    gap: 12px;
  }
  .wordmark__dot {
    width: 18px;
    height: 18px;
    border-radius: 50%;
    background: var(--brand-blue);
  }
  .card--front .wordmark {
    font-size: 92px;
    margin-top: 150px;
  }
  .identity {
    margin-top: 200px;
    text-align: center;
  }
  .identity__name {
    color: var(--brand-blue);
    font-weight: 700;
    font-size: 34px;
    letter-spacing: 0.5px;
  }
  .identity__role {
    color: var(--ink-light);
    font-size: 20px;
    margin-top: 4px;
  }
  .contact-icons {
    display: flex;
    align-items: center;
    gap: 8px;
    margin-top: 22px;
  }
  .contact-icons__rule {
    width: 50px;
    height: 1px;
    background: var(--rule);
  }
  .contact-icons svg {
    width: 30px;
    height: 30px;
    display: block;
  }
  .contact-list {
    list-style: none;
    text-align: center;
    color: var(--ink-light);
    font-size: 21px;
    line-height: 1.5;
    margin-top: 14px;
  }
  .card--back {
    background: radial-gradient(circle at 40% 40%, var(--brand-blue-light), var(--brand-blue) 55%, var(--brand-blue-deep));
  }
  .card--back .wordmark {
    position: absolute;
    left: 0;
    right: 0;
    bottom: 190px;
    justify-content: center;
    font-size: 96px;
  }
  .card--back .wordmark__dot { background: var(--ink-light); }
</style>
</head>
<body>
<main class="stage">
  <section class="card card--front" aria-label="Card front">
    <div class="wordmark"><span class="wordmark__dot"></span>Petalon</div>
    <div class="identity">
      <div class="identity__name">MARTIN COLE</div>
      <div class="identity__role">Founder/ CEO</div>
    </div>
    <div class="contact-icons">
      <span class="contact-icons__rule"></span>
      <svg viewBox="0 0 30 30" aria-label="Phone">
        <circle cx="15" cy="15" r="13" fill="none" stroke="var(--brand-blue)" stroke-width="2.5"/>
        <path d="M11 9c-1 1-1.5 2.5 0 5s4 5 6 6c1.5.7 2.5 0 3.5-1l-2-2-1.5 1c-1.5-.8-3-2.5-3.8-3.8l1-1.5z" fill="var(--brand-blue)"/>
      </svg>
      <svg viewBox="0 0 30 30" aria-label="Email">
        <circle cx="15" cy="15" r="13" fill="none" stroke="var(--brand-blue)" stroke-width="2.5"/>
        <rect x="8.5" y="10.5" width="13" height="9" fill="none" stroke="var(--brand-blue)" stroke-width="1.8"/>
        <path d="M8.5 10.5l6.5 5 6.5-5" fill="none" stroke="var(--brand-blue)" stroke-width="1.8"/>
      </svg>
      <svg viewBox="0 0 30 30" aria-label="Website">
        <circle cx="15" cy="15" r="13" fill="none" stroke="var(--brand-blue)" stroke-width="2.5"/>
        <circle cx="15" cy="15" r="7" fill="none" stroke="var(--brand-blue)" stroke-width="1.6"/>
        <ellipse cx="15" cy="15" rx="3" ry="7" fill="none" stroke="var(--brand-blue)" stroke-width="1.4"/>
        <path d="M8 15h14" stroke="var(--brand-blue)" stroke-width="1.4"/>
      </svg>
      <span class="contact-icons__rule"></span>
    </div>
    <ul class="contact-list">
      <li>555-204-7816</li>
      <li>martin.cole@petalon.one</li>
      <li>www.Petalon.one</li>
    </ul>
  </section>

  <section class="card card--back" role="img" aria-label="Card back: blue field with a scattered pattern of dots and rings, with the Petalon name">
    <div class="wordmark"><span class="wordmark__dot"></span>Petalon</div>
  </section>
</main>
</body>
</html>
```